Business card for Luxury Portable Restroom Trailer company

We are a Luxury Portable Restroom Trailer Company Called FALCRIDGE HIRES. Based in Orange County California. We provide portable restroom trailers for events, such as, Weddings, Concerts, Charity events, Sporting events, Tournaments, Corporate events, ect. We rent and Sell the Luxury restrooms. Our colors are white, grey, and Orange. As you will see in the logo we uploaded.
There are 2 people in the company so the names and titles will change for the 3 people but card will remain the same. Here is the information for each Person: Dwight Penner CFO 555 318-0476
next Person: Leon Marchetti VP 555 318-0476
Next Person: Owen Marchetti CEO 555 318-0476
Information to include on the card: Luxury Restroom Trailers Rental and Sales. Weddings, Concerts, Charity, Sporting and Corp. Events.

```html
<!DOCTYPE html>
<html lang="en">
<head>
<meta charset="utf-8">
<title>FALCRIDGE HIRES – Business Card</title>
<link href="https://fonts.googleapis.com/css2?family=Montserrat:wght@400;500;600;800&display=swap" rel="stylesheet">
<style>
  :root {
    --orange: #ee6a26;
    --orange-light: #f5965f;
    --grey-dark: #4a4a4c;
    --grey-text: #55565a;
    --card-white: #f3f3f3;
    --stage: #d9d9d9;
  }
  * { box-sizing: border-box; margin: 0; padding: 0; }
  html, body { width: 1200px; height: 1200px; overflow: hidden; }
  body {
    background: var(--stage);
    font-family: "Montserrat", sans-serif;
    display: flex;
    flex-direction: column;
    align-items: center;
    justify-content: center;
    gap: 60px;
  }
  .card {
    width: 840px;
    height: 480px;
    border-radius: 26px;
    overflow: hidden;
    position: relative;
    box-shadow: 0 10px 24px rgba(0,0,0,0.18);
  }

  /* Back side */
  .card-back {
    background: var(--orange);
  }
  .card-back .pattern-area {
    position: absolute;
    inset: 0;
    background: linear-gradient(100deg, var(--orange-light) 0%, var(--orange) 55%, var(--orange) 100%);
  }
  .card-back .brand {
    position: absolute;
    right: 90px;
    top: 222px;
    display: flex;
    align-items: center;
    gap: 12px;
  }
  .brand-mark {
    width: 22px;
    height: 22px;
    background: #ffffff;
  }
  .card-back .brand-name {
    color: #ffffff;
    font-weight: 800;
    font-size: 34px;
    letter-spacing: 1px;
  }

  /* Front side */
  .card-front {
    background: var(--card-white);
  }
  .front-brand {
    position: absolute;
    top: 70px;
    left: 0;
    right: 0;
    display: flex;
    justify-content: center;
    align-items: center;
    gap: 16px;
  }
  .front-brand .brand-mark { background: var(--orange); width: 30px; height: 30px; }
  .front-brand .brand-name {
    color: var(--orange);
    font-weight: 800;
    font-size: 58px;
    letter-spacing: 1px;
  }
  .services {
    position: absolute;
    top: 168px;
    left: 0;
    right: 0;
    text-align: center;
    color: var(--grey-text);
    font-size: 21px;
    line-height: 1.4;
    font-weight: 400;
  }
  .details {
    position: absolute;
    top: 262px;
    left: 0;
    right: 0;
    display: flex;
    justify-content: center;
    align-items: center;
    gap: 26px;
  }
  .person { text-align: right; }
  .person-name {
    color: var(--orange);
    font-weight: 600;
    font-size: 33px;
    line-height: 1.1;
  }
  .person-title {
    color: var(--grey-text);
    font-size: 22px;
    font-weight: 400;
    margin-top: 4px;
  }
  .divider {
    width: 2px;
    height: 90px;
    background: var(--grey-dark);
  }
  .contacts { list-style: none; }
  .contacts li {
    display: flex;
    align-items: center;
    gap: 12px;
    color: var(--grey-text);
    font-size: 21px;
    line-height: 1.5;
  }
  .contacts svg { width: 18px; height: 18px; flex: none; }
  .address-band {
    position: absolute;
    left: 0; right: 0; bottom: 0;
    height: 64px;
    background: var(--grey-dark);
    color: #ffffff;
    display: flex;
    align-items: center;
    justify-content: center;
    font-size: 21px;
    font-weight: 500;
    letter-spacing: 0.3px;
  }
</style>
</head>
<body>

  <section class="card card-back">
    <div class="pattern-area" role="img" aria-label="Repeating embossed brand emblem pattern on an orange gradient"></div>
    <div class="brand">
      <span class="brand-mark"></span>
      <span class="brand-name">FALCRIDGE HIRES</span>
    </div>
  </section>

  <section class="card card-front">
    <div class="front-brand">
      <span class="brand-mark"></span>
      <span class="brand-name">FALCRIDGE HIRES</span>
    </div>

    <p class="services">
      Luxury Restroom | Trailers Rental and Sales | Weddings |<br>
      Concerts | Charity | Sporting and Corp. Events
    </p>

    <div class="details">
      <div class="person">
        <div class="person-name">Dwight Penner</div>
        <div class="person-title">CFO</div>
      </div>
      <div class="divider"></div>
      <ul class="contacts">
        <li>
          <svg viewBox="0 0 24 24" aria-hidden="true"><path fill="#ee6a26" d="M6.6 10.8a15.1 15.1 0 0 0 6.6 6.6l2.2-2.2a1 1 0 0 1 1-.25 11.4 11.4 0 0 0 3.6.57 1 1 0 0 1 1 1V20a1 1 0 0 1-1 1A17 17 0 0 1 3 4a1 1 0 0 1 1-1h3.5a1 1 0 0 1 1 1c0 1.25.2 2.45.57 3.57a1 1 0 0 1-.25 1z"/></svg>
          555 318-0476
        </li>
        <li>
          <svg viewBox="0 0 24 24" aria-hidden="true"><rect x="2" y="5" width="20" height="14" rx="1.5" fill="#ee6a26"/><path d="M3 6l9 7 9-7" fill="none" stroke="#ffffff" stroke-width="1.8"/></svg>
          info@falcridgehires.com
        </li>
        <li>
          <svg viewBox="0 0 24 24" aria-hidden="true"><circle cx="12" cy="12" r="10" fill="#ee6a26"/><path d="M2 12h20M12 2c3 3 3 17 0 20M12 2c-3 3-3 17 0 20" fill="none" stroke="#ffffff" stroke-width="1.4"/></svg>
          www.falcridgehires.com
        </li>
      </ul>
    </div>

    <div class="address-band">7415 Elmbrook Road Lake Alder Maine 11458</div>
  </section>

</body>
</html>
```